Updated website design needed for Radiology Group, Pine Hollow Imaging Partners

Clean, uncluttered, updated design needed for top regional Radiology Center. Focus on personal, patient oriented design, (not clinical). Should be simple and easy to navigate, with clear CTAs. Use blues, greens and photos of people in the Central Oregon outdoors.
Uncoded, PSD design only. 2 pages: Home page and one example interior page.
reference current site: http://www.phipclinic-example.com/
Sites they like:
http://www.valescanlabs-example.com/
http://www.tbmx-example.net/handler.cfm?event=practice,main
http://www.kestrelbonecare-example.com/

Medical Imaging

2 page

Sans Serif

• Personal and patient friendly.
• Lots of white space, clean and uncluttered. Clear CTAs, such as: Patient Bill Pay, Make an Appointment, Meet Our Doctors
• Use copy and contact information from the current site.
• Use outdoor images from Central Oregon, late Winter/ Spring (snow, light colors, spring green, for example)
• Include one example interior page, either Your Exam or Meet Our Doctors
• The client likes:
• Meet Our Doctors slider section, and big, easy to navigate Information Center on www.kestrelbonecare-example.com
• The personal feel of the Your Exam section on www.valescanlabs-example.com
• Blues and Greens, outdoorsy imagery
• The client does not like:
• complex drop down menus
• clinical feel
• Do not use lorum ipsum or dummy text.
• Do not use outdoor images from other regions. Do not use Summer (hot, poolside) or Fall (red/orange leaves) images.

```html
<!DOCTYPE html>
<html lang="en">
<head>
<meta charset="utf-8">
<title>Pine Hollow Imaging Partners – Our Service</title>
<link rel="stylesheet" href="https://fonts.googleapis.com/css2?family=Questrial&family=Lato:wght@400;700&family=Open+Sans:wght@400;600&display=swap">
<style>
:root{
  --navy:#0c2a5e;
  --navy-deep:#0a2252;
  --blue:#1d5d8f;
  --blue-btn:#1e5f8e;
  --blue-active:#2b6ea6;
  --heading:#1b5a8c;
  --text:#555b63;
  --muted:#8a8f96;
  --tick:#1e5f8e;
  --grey-band:#f1f1f1;
  --grey-band2:#e9e9e9;
  --line:#c8ccd2;
  --white:#ffffff;
}
*{margin:0;padding:0;box-sizing:border-box}
html,body{width:1200px;height:2707px;overflow:hidden}
body{position:relative;background:var(--white);font-family:'Lato',sans-serif;color:var(--text)}
.abs{position:absolute}

/* header */
.site-header{left:0;top:0;width:1200px;height:108px;background:var(--white)}
.brand{left:47px;top:20px;display:flex;align-items:center;gap:14px}
.brand-mark{width:52px;height:52px;background:var(--navy)}
.brand-name{font-family:'Lato',sans-serif;font-weight:700;font-size:21px;line-height:1.15;color:var(--navy);width:200px}
.contact-btn{top:25px;height:58px;background:var(--blue-btn);border:2px solid #4d86b4;color:var(--white);font-family:'Open Sans',sans-serif;padding:6px 0 0 16px}
.contact-btn .lbl{font-size:17px;font-weight:600;display:block;line-height:1.1}
.contact-btn .num{font-size:13px;display:flex;align-items:center;gap:4px;margin-top:3px}
.contact-btn svg{width:10px;height:10px}

/* nav */
.main-nav{left:0;top:108px;width:1200px;height:63px;background:var(--navy);display:flex;align-items:stretch;padding-left:50px;font-family:'Open Sans',sans-serif;font-size:13.5px;color:var(--white)}
.main-nav a{color:var(--white);text-decoration:none;display:flex;align-items:center;padding:0 17px}
.main-nav .sep{display:flex;align-items:center;color:#b5c2d6}
.main-nav a.active{background:var(--blue-active)}

/* hero */
.hero{left:0;top:171px;width:1200px;height:517px;background:linear-gradient(180deg,#2f6fb7 0%,#5a97d2 40%,#a9cbe8 70%,#dfe8ef 100%)}
.hero-title{left:44px;top:115px;font-family:'Questrial',sans-serif;font-size:44px;line-height:53px;color:var(--white);letter-spacing:2px;font-weight:400;text-shadow:0 0 1px #fff}
.hero-text{left:47px;top:226px;width:590px;font-size:14px;line-height:22px;color:var(--white)}
.btn{background:var(--navy);color:var(--white);font-family:'Open Sans',sans-serif;font-size:12px;text-transform:uppercase;display:flex;align-items:center;justify-content:center;letter-spacing:.3px}
.hero-btn{left:47px;top:318px;width:128px;height:43px;text-transform:none;font-size:12px}
.hero-dots{left:50px;top:383px;display:flex;gap:9px}
.hero-dots span{width:14px;height:14px;border:1.5px solid #e8eef6;border-radius:50%}
.hero-dots span.on{background:#e8eef6}

/* intro */
.section-head{left:47px;top:718px;width:1108px;display:flex;align-items:center;gap:12px}
.section-head .rule{flex:1;height:1px;background:#9aa3ad;position:relative}
.section-head .rule::after{content:"";position:absolute;top:-5px;width:9px;height:9px;border:1.5px solid #9aa3ad;border-radius:50%;background:#fff}
.section-head .rule.l::after{right:0}
.section-head .rule.r::after{left:0}
.section-head h2{font-family:'Questrial',sans-serif;font-weight:400;font-size:32px;color:var(--heading);letter-spacing:1px}
.intro{left:120px;top:784px;width:960px;text-align:center;font-size:12.5px;line-height:23px;color:var(--muted)}

/* service bands */
.band{left:0;width:1200px}
.band.grey{background:var(--grey-band)}
.band.grey2{background:var(--grey-band2)}
.photo-frame{background:var(--white);border:1px solid #d4d6d9;padding:9px}
.photo-frame div{width:100%;height:100%}
.service-title{font-family:'Questrial',sans-serif;font-weight:400;font-size:24px;color:var(--heading);letter-spacing:1px;padding-bottom:10px;border-bottom:1.5px solid var(--line)}
.checklist{list-style:none;font-size:15.5px;color:var(--text)}
.checklist li{position:relative;padding-left:28px;height:41px;line-height:20px}
.checklist li.two{height:62px}
.checklist li::before{content:"";position:absolute;left:3px;top:3px;width:5px;height:10px;border:solid var(--tick);border-width:0 2.5px 2.5px 0;transform:rotate(40deg)}
.checklist li.hl{color:var(--blue)}
.read-more{width:138px;height:34px}

/* footer */
.site-footer{left:0;top:2328px;width:1200px;height:283px;background:linear-gradient(180deg,#1d6c9c 0%,#1c5f92 100%);color:var(--white)}
.f-col{top:42px}
.f-col h3{font-family:'Questrial',sans-serif;font-weight:400;font-size:17px;margin-bottom:14px}
.f-col ul{list-style:none;font-size:12px;line-height:29px}
.f-col li::before{content:"•";margin-right:10px}
.f-col li.more{font-weight:700;padding-left:12px}
.f-col li.more::before{content:""}
.f-col b{font-weight:700}
.f-div{top:0;width:1px;height:283px;background:rgba(255,255,255,.16)}
.bottom-bar{left:0;top:2611px;width:1200px;height:96px;background:var(--navy-deep);color:var(--white);font-size:12px}
.copyright{left:47px;top:41px}
.social{top:33px;width:30px;height:30px;border:1.5px solid var(--white)}
</style>
</head>
<body>

<header class="abs site-header">
  <div class="abs brand">
    <div class="brand-mark"></div>
    <div class="brand-name">Pine Hollow Imaging Partners</div>
  </div>
  <div class="abs contact-btn" style="left:480px;width:171px"><span class="lbl">Medical Records:</span><span class="num"><svg viewBox="0 0 10 10"><path d="M2 1l2 2-1 1.5a6 6 0 0 0 2.5 2.5L7 6l2 2-1.5 1.5C4 9 1 6 .5 2z" fill="#fff"/></svg>+ (555) 010-4977</span></div>
  <div class="abs contact-btn" style="left:664px;width:157px"><span class="lbl">Billing:</span><span class="num"><svg viewBox="0 0 10 10"><path d="M2 1l2 2-1 1.5a6 6 0 0 0 2.5 2.5L7 6l2 2-1.5 1.5C4 9 1 6 .5 2z" fill="#fff"/></svg>+ (555) 010-4614</span></div>
  <div class="abs contact-btn" style="left:834px;width:155px"><span class="lbl">Scheduling:</span><span class="num"><svg viewBox="0 0 10 10"><path d="M2 1l2 2-1 1.5a6 6 0 0 0 2.5 2.5L7 6l2 2-1.5 1.5C4 9 1 6 .5 2z" fill="#fff"/></svg>+ (555) 010-2383</span></div>
  <div class="abs contact-btn" style="left:1000px;width:155px"><span class="lbl">Main Line:</span><span class="num"><svg viewBox="0 0 10 10"><path d="M2 1l2 2-1 1.5a6 6 0 0 0 2.5 2.5L7 6l2 2-1.5 1.5C4 9 1 6 .5 2z" fill="#fff"/></svg>+ (555) 010-2633</span></div>
</header>

<nav class="abs main-nav">
  <a href="#">Home</a><span class="sep">|</span>
  <a href="#">About Us</a><span class="sep">|</span>
  <a href="#" class="active">Our Service</a><span class="sep">|</span>
  <a href="#">For Patients</a><span class="sep">|</span>
  <a href="#">Our Physicians</a><span class="sep">|</span>
  <a href="#">For Physicians</a><span class="sep">|</span>
  <a href="#">PACS &amp; Document</a><span class="sep">|</span>
  <a href="#">Appointment</a><span class="sep">|</span>
  <a href="#">Our Location</a>
</nav>

<section class="abs hero" role="img" aria-label="Group of smiling skiers and snowboarders celebrating in the snowy mountains under a blue sky">
  <h1 class="abs hero-title">Welcome to Pine Hollow<br>Imaging Partners</h1>
  <p class="abs hero-text">Pine Hollow Imaging Partners is a diagnostic imaging corporation providing professional services to Central and Eastern Oregon hospitals and clinics as well as state-of-the-art services in its' own outpatient imaging center.</p>
  <a class="abs btn hero-btn">Read More</a>
  <div class="abs hero-dots"><span></span><span></span><span class="on"></span><span></span><span></span></div>
</section>

<div class="abs section-head"><span class="rule l"></span><h2>Our Service</h2><span class="rule r"></span></div>
<p class="abs intro">Our state-of-the-art outpatient imaging center provides professional services to Central Oregon Hospitals and Clinics. Pine Hollow Imaging is staffed with fellowship trained physicians with expertise in diagnostic and interventional procedures. Our technologists have advanced level training and certification in each imaging modality they specialize in. Each of our imaging modalities has either been granted National Imaging Accreditation Board accreditation or is in the process of doing so. This rigorous process provides a stamp of approval for the entire imaging process, including the equipment, quality control program, record keeping and staff qualifications.</p>

<!-- General Radiology -->
<section class="abs band grey" style="top:942px;height:348px">
  <div class="abs photo-frame" style="left:47px;top:38px;width:353px;height:263px"><div role="img" aria-label="X-ray image of two hands" style="background:radial-gradient(ellipse at center,#8c8c8c 0%,#2a2a2a 55%,#050505 100%)"></div></div>
  <h3 class="abs service-title" style="left:430px;top:30px;width:725px">General Radiology (X-Ray)</h3>
  <ul class="abs checklist" style="left:430px;top:97px">
    <li class="hl">Head, chest, abdomen</li><li>Upper &amp; lower extremity</li><li>Fluoroscopy:</li><li>Upper GI, Small Bowel Follow-Through</li>
  </ul>
  <ul class="abs checklist" style="left:816px;top:97px">
    <li>Barium Enema</li><li>Myelography</li><li>Hysterosalpingography</li><li>Arthrography</li>
  </ul>
  <a class="abs btn read-more" style="left:435px;top:268px">Read More</a>
</section>

<!-- Digital Mammography -->
<section class="abs band" style="top:1290px;height:347px">
  <h3 class="abs service-title" style="left:49px;top:34px;width:722px">Digital Mammography</h3>
  <ul class="abs checklist" style="left:49px;top:100px">
    <li>Ductography</li><li>Needle localizations</li><li>Computed Aided Detection (CAD)</li><li>Screeening</li>
  </ul>
  <ul class="abs checklist" style="left:420px;top:100px">
    <li>Diagnostic</li><li>Stereotactic biopsy</li>
  </ul>
  <a class="abs btn read-more" style="left:49px;top:270px">Read More</a>
  <div class="abs photo-frame" style="left:801px;top:42px;width:350px;height:263px"><div role="img" aria-label="Technician at a screen beside a mammography machine in a bright room" style="background:linear-gradient(135deg,#e8eef3 0%,#cfdde8 50%,#f4f6f8 100%)"></div></div>
</section>

<!-- Ultrasound -->
<section class="abs band grey2" style="top:1637px;height:348px">
  <div class="abs photo-frame" style="left:47px;top:36px;width:353px;height:263px"><div role="img" aria-label="Pregnant patient receiving an ultrasound scan" style="background:linear-gradient(135deg,#e9e4e0 0%,#cfc7d6 50%,#f2efec 100%)"></div></div>
  <h3 class="abs service-title" style="left:432px;top:30px;width:723px">Ultrasound</h3>
  <ul class="abs checklist" style="left:432px;top:96px">
    <li>Obstetrical</li><li>Gynecological/pelvic</li><li>Abdomen</li><li>Vascular – including venous &amp; arterial</li>
  </ul>
  <ul class="abs checklist" style="left:816px;top:96px">
    <li>Breast</li><li>Thyroid</li><li>Scrotal</li><li>Biopsies</li>
  </ul>
  <a class="abs btn read-more" style="left:435px;top:266px">Read More</a>
</section>

<!-- Nuclear Medicine -->
<section class="abs band" style="top:1985px;height:343px">
  <h3 class="abs service-title" style="left:47px;top:35px;width:724px">Nuclear Medicine and Position Emission Tomography</h3>
  <ul class="abs checklist" style="left:47px;top:101px">
    <li>Bone scan – whole body and three phase</li><li class="two">Hepatobiliary scans – with &amp; without<br>ejection fraction</li><li>Gastric emptying</li><li>Lymphoscintigraphy</li>
  </ul>
  <ul class="abs checklist" style="left:420px;top:101px">
    <li>SPECT</li><li>PET</li>
  </ul>
  <a class="abs btn read-more" style="left:47px;top:272px">Read More</a>
  <div class="abs photo-frame" style="left:801px;top:42px;width:355px;height:263px"><div role="img" aria-label="Patient lying on a scanner table entering a PET scanner" style="background:linear-gradient(135deg,#2f6f91 0%,#d9d2c2 45%,#efe9dc 100%)"></div></div>
</section>

<footer class="abs site-footer">
  <div class="abs f-div" style="left:329px"></div>
  <div class="abs f-div" style="left:611px"></div>
  <div class="abs f-div" style="left:892px"></div>
  <div class="abs f-col" style="left:52px">
    <h3>For Patients</h3>
    <ul><li>About Your Visit</li><li>Why Choose Us?</li><li>Patient Forms</li><li>Billing and Insurance</li><li class="more">More +</li></ul>
  </div>
  <div class="abs f-col" style="left:359px">
    <h3>Quick Links</h3>
    <ul><li>About Us</li><li>Our Physicians</li><li>For Physicians</li><li>Disclaimer</li><li class="more">More +</li></ul>
  </div>
  <div class="abs f-col" style="left:641px;top:38px">
    <h3>Our Services</h3>
    <ul><li>Mammography</li><li>MRI</li><li>CT-64</li><li>X-Ray</li><li class="more">More +</li></ul>
  </div>
  <div class="abs f-col" style="left:926px">
    <h3>Contact Us</h3>
    <ul><li>(555) 010-2633 - <b>Main Line</b></li><li>(555) 010-2383 - <b>Scheduling</b></li><li>(555) 010-4614 - <b>Billing</b></li><li>(555) 010-4977 - <b>Medical Records</b></li></ul>
  </div>
</footer>

<div class="abs bottom-bar">
  <p class="abs copyright">Copyright 2016 Company Name.  All Rights Reserved.</p>
  <span class="abs social" style="left:1039px" aria-label="Social link"></span>
  <span class="abs social" style="left:1082px" aria-label="Social link"></span>
  <span class="abs social" style="left:1124px" aria-label="Social link"></span>
</div>

</body>
</html>
```